Kestrel Facilities Business Card Design

We would now like to design business cards with the new Kestrel Facilities logo

Target Market(s)

Professional

Industry/Entity Type

Professional services

Contact Information for Business Card

Employee name, title, phone number, email address, corporate office address and logo.

Font styles to use
Sans Serif

Colors
0054AA
0677BA
7BADD7
CADEEF
E8F1F8

Requirements
Must have
• My logo
Should not have
• any other pictures or images besides my logo

```html
<!DOCTYPE html>
<html lang="en">
<head>
<meta charset="utf-8">
<title>Kestrel Facilities Business Card</title>
<link href="https://fonts.googleapis.com/css2?family=Oswald:wght@600&family=Montserrat:wght@400;500&display=swap" rel="stylesheet">
<style>
  :root {
    --brand-blue: #2c6aa8;
    --brand-blue-deep: #235a93;
    --brand-blue-light: #3479bd;
    --accent-blue: #2f70b8;
    --card-white: #ffffff;
    --card-shade: #eeeeee;
    --ink: #2a2a2a;
    --logo-ink: #d6dde4;
    --backdrop: #3a3c40;
  }
  html, body {
    margin: 0;
    width: 1200px;
    height: 900px;
    overflow: hidden;
    background: var(--backdrop);
  }
  .canvas {
    width: 1200px;
    height: 900px;
    display: flex;
    flex-direction: column;
    align-items: center;
    justify-content: center;
    gap: 40px;
  }
  .card {
    width: 700px;
    height: 400px;
    box-sizing: border-box;
    box-shadow: 0 12px 28px rgba(0,0,0,0.45);
    position: relative;
  }
  .card-front {
    background: radial-gradient(ellipse at 55% 45%, var(--card-white) 40%, var(--card-shade) 100%);
    display: flex;
    align-items: center;
  }
  .identity {
    width: 330px;
    text-align: right;
  }
  .person-name {
    font-family: "Oswald", sans-serif;
    font-weight: 600;
    font-size: 52px;
    line-height: 1;
    color: var(--accent-blue);
    text-transform: uppercase;
    letter-spacing: -0.5px;
    margin: 0;
  }
  .person-title {
    font-family: "Montserrat", sans-serif;
    font-size: 18px;
    color: var(--ink);
    margin: 6px 2px 0 0;
  }
  .divider {
    width: 2px;
    height: 150px;
    background: var(--accent-blue);
    margin: 30px 0 0 30px;
  }
  .contact {
    font-family: "Montserrat", sans-serif;
    font-size: 17px;
    line-height: 1.45;
    color: var(--ink);
    margin: 40px 0 0 26px;
    padding: 0;
    list-style: none;
  }
  .contact li {
    display: flex;
    align-items: center;
    gap: 8px;
  }
  .contact .icon {
    width: 14px;
    height: 14px;
    flex: none;
  }
  .card-back {
    background: linear-gradient(135deg, var(--brand-blue-deep) 0%, var(--brand-blue-light) 55%, var(--brand-blue) 100%);
    display: flex;
    align-items: center;
    justify-content: center;
    gap: 22px;
  }
  .brand-mark {
    width: 64px;
    height: 64px;
    background: var(--logo-ink);
  }
  .brand-name {
    font-family: "Oswald", sans-serif;
    font-weight: 600;
    font-size: 58px;
    color: var(--logo-ink);
    text-transform: uppercase;
    letter-spacing: 3px;
    margin: 0;
  }
</style>
</head>
<body>
<main class="canvas">
  <section class="card card-front" aria-label="Business card front">
    <div class="identity">
      <h1 class="person-name">Martin Caldwell</h1>
      <p class="person-title">Director</p>
    </div>
    <div class="divider"></div>
    <ul class="contact">
      <li>1187 Larkspur Lane</li>
      <li>Salem, OR 97302</li>
      <li>
        <svg class="icon" viewBox="0 0 16 16" aria-hidden="true"><path d="M4 1.5l2 3-1.3 1.3c.8 1.8 2.2 3.2 4 4L10 8.5l3 2-1.2 2.8C7 13 3 9 2.7 4.2z" fill="var(--accent-blue)"/></svg>
        (555) 204-6618
      </li>
      <li>
        <svg class="icon" viewBox="0 0 16 16" aria-hidden="true"><rect x="1.5" y="3.5" width="13" height="9" fill="none" stroke="var(--accent-blue)" stroke-width="1.4"/><path d="M1.5 3.5L8 9l6.5-5.5" fill="none" stroke="var(--accent-blue)" stroke-width="1.4"/></svg>
        info@kestrelfacilities.com
      </li>
    </ul>
  </section>
  <section class="card card-back" aria-label="Business card back">
    <div class="brand-mark"></div>
    <p class="brand-name">Kestrel Facilities</p>
  </section>
</main>
</body>
</html>
```